Business card for law firm

Need business card for new law firm. Think confident, authoritative, conservative, but not stuffy or old-fashioned.

Contact Information for Business Card

Content for card - logo (uploaded), plus the following:

Paul Whitcombe (larger font)
Managing Partner (larger font, but not as large as name)
Level 9, 7 Ferris Lane
Sydney NSW 2000
Main Tel 02 9364 2710
Direct Tel 02 8472 3159
Email paul@qvlegal.com.au
www.qvlegal.com.au

Letterhead design should include logo plus:
Level 9, 7 Ferris Lane
Sydney NSW 2000
Tel 02 8472 3159
www.qvlegal.com.au

```html
<!DOCTYPE html>
<html lang="en">
<head>
<meta charset="utf-8">
<title>Quayvale Legal — Letterhead</title>
<link href="https://fonts.googleapis.com/css2?family=Questrial&family=Roboto:wght@400&display=swap" rel="stylesheet">
<style>
  :root {
    --backdrop: #e4e4e4;
    --paper: #f1f1f1;
    --paper-edge: #dcdcdc;
    --navy: #1b2c6b;
    --ink-soft: #8c8c8c;
    --ink-body: #8a8a8a;
    --signature-blue: #3a63b8;
  }
  * { margin: 0; padding: 0; box-sizing: border-box; }
  html, body {
    width: 1024px;
    height: 1200px;
    overflow: hidden;
    background: var(--backdrop);
  }
  .letterhead {
    position: absolute;
    left: 152px;
    top: 96px;
    width: 719px;
    height: 1008px;
    background: linear-gradient(90deg, #f3f3f3 0%, #ececec 60%, #e6e6e6 100%);
    border: 1px solid var(--paper-edge);
    font-family: "Questrial", "Century Gothic", sans-serif;
  }
  .brand {
    position: absolute;
    left: 64px;
    top: 72px;
    display: flex;
    align-items: center;
    gap: 10px;
  }
  .brand-mark {
    width: 14px;
    height: 14px;
    background: var(--navy);
  }
  .brand-name {
    font-size: 20px;
    letter-spacing: 2px;
    color: var(--navy);
    text-transform: uppercase;
  }
  .salutation {
    position: absolute;
    left: 67px;
    top: 262px;
    font-size: 17px;
    color: var(--ink-soft);
  }
  .letter-body {
    position: absolute;
    left: 67px;
    top: 313px;
    width: 594px;
    font-size: 10.3px;
    line-height: 13.4px;
    color: var(--ink-body);
    text-align: justify;
    hyphens: auto;
  }
  .letter-body p { margin-bottom: 13.4px; }
  .closing {
    position: absolute;
    left: 67px;
    top: 638px;
    font-size: 10.3px;
    color: var(--ink-body);
  }
  .signature {
    position: absolute;
    left: 67px;
    top: 697px;
    width: 125px;
    height: 54px;
    background: linear-gradient(90deg, rgba(58,99,184,0.18), rgba(58,99,184,0.08));
    border-radius: 4px;
  }
  .footer-rule {
    position: absolute;
    left: 67px;
    top: 922px;
    width: 594px;
    height: 1px;
    background: var(--navy);
  }
  .footer {
    position: absolute;
    left: 67px;
    top: 931px;
    width: 594px;
    display: flex;
    justify-content: space-between;
    font-family: "Roboto", Arial, sans-serif;
    font-size: 12.5px;
    line-height: 15px;
    color: var(--navy);
  }
  .footer-address { text-align: right; }
</style>
</head>
<body>
  <main class="letterhead">
    <div class="brand">
      <span class="brand-mark"></span>
      <span class="brand-name">Quayvale Legal</span>
    </div>

    <p class="salutation">Dear Mr. Hale,</p>

    <div class="letter-body">
      <p>Lorem ipsum dolor sit amet, consectetur adipiscing elit. Donec orci purus, luctus vitae dignissim eu, iaculis sed purus. Vivamus faucibus, ipsum nec aliquet viverra, leo mauris condimentum ligula, sit amet sagittis enim ligula quis arcu. Nam egestas tortor id nisi porttitor mattis. In tortor ante, ultricies in suscipit a, tempus non massa. Vivamus et auctor mi. Fusce vel massa nulla. Phasellus nec eros mauris, et scelerisque orci.</p>
      <p>Donec malesuada orci vitae nulla accumsan porta a id massa. Quisque accumsan iaculis magna sit amet fringilla. Maecenas consequat, magna eget tincidunt semper, odio nibh rutrum mi, id feugiat ante nisi eu risus. Vestibulum nunc orci, rhoncus a placerat in, ultricies in mi. Cras mattis varius eros, vel fringilla nisi suscipit eget. Quisque scelerisque sagittis nulla at porttitor.</p>
      <p>Sed id augue vitae urna euismod commodo aliquet a quam. Pellentesque arcu velit, cursus et malesuada ut, consequat et diam. Nullam erat sem, rhoncus id ullamcorper vitae, rhoncus et arcu. In ultricies ultricies nulla, ut rutrum nisi iaculis at. Donec eu magna a metus ornare faucibus. Fusce aliquet faucibus ultricies. Morbi semper, est id tincidunt gravida, sem arcu adipiscing lacus, ac bibendum nulla leo eu purus. Quisque nec diam sed risus consectetur a ccumsan quis quis nibh. Vestibulum id purus lorem.</p>
      <p>It is a long established fact that a reader will be distracted by the readable content of a page when looking at its layout. The point of using Lorem Ipsum is that it has a more-or-less normal distribution of letters, as opposed to using 'Content here, content here', making it look like readable English. Many desktop publishing packages</p>
    </div>

    <p class="closing">Sincerely,</p>

    <div class="signature" role="img" aria-label="Handwritten signature of the sender in blue ink"></div>

    <div class="footer-rule"></div>
    <footer class="footer">
      <div class="footer-contact">
        www.qvlegal.com.au<br>
        02 8472 3159
      </div>
      <div class="footer-address">
        Level 9, 7 Ferris Lane<br>
        Sydney NSW 2000
      </div>
    </footer>
  </main>
</body>
</html>
```